ReelBloom business card

We are a performing arts company providing training (to both kids and adults) as well as performers for events. We hope to bring joy and confidence on stage to the people we train, as well as joy to the audience when our artistes perform. Designs should convey the joy, confidence and vibrancy on stage. Design business card using the attached logo. Card to include name, mobile tel, email address, company address, and website. Double sided. To also include the following list of what the company does:
• Training & Enrichment
• Private & Corporate Entertainment
- Music composition & production

Industry/Entity Type

Training

Contact Information for Business Card

Card to include name, mobile tel, email address, company address, and website. Double sided. To also include the following list of what the company does:
• Training & Enrichment

Requirements
Nice to have
• Card need not be the traditional rectangular in shape but not too outrageous.

```html
<!DOCTYPE html>
<html lang="en">
<head>
<meta charset="utf-8">
<title>ReelBloom business card</title>
<link rel="stylesheet" href="https://fonts.googleapis.com/css2?family=Arimo:wght@400;700&display=swap">
<style>
  :root {
    --page: #ecebe8;
    --card: #ffffff;
    --ink: #111111;
    --brand: #2e2f86;
    --accent: #e2262f;
    --deco-light: #f3f3f3;
    --deco-mid: #e3e3e3;
    --shadow: rgba(0, 0, 0, 0.18);
  }
  * { box-sizing: border-box; margin: 0; padding: 0; }
  html, body { width: 1200px; height: 848px; overflow: hidden; }
  body {
    background: var(--page);
    font-family: "Arimo", Arial, sans-serif;
    color: var(--ink);
    display: flex;
    align-items: center;
    justify-content: center;
    gap: 48px;
  }
  .card {
    position: relative;
    width: 540px;
    height: 310px;
    background: var(--card);
    border-radius: 26px;
    box-shadow: 0 10px 26px var(--shadow);
    overflow: hidden;
  }
  .music-staff {
    position: absolute;
    left: 60px;
    top: 60px;
    width: 470px;
    height: 230px;
    border-radius: 50% 40% 50% 40%;
    background: radial-gradient(ellipse at 45% 55%, var(--deco-mid) 0%, var(--deco-light) 55%, rgba(255,255,255,0) 75%);
  }
  .brand {
    position: absolute;
    top: 56px;
    right: 40px;
    display: flex;
    align-items: center;
    gap: 10px;
  }
  .brand-dot {
    width: 22px;
    height: 22px;
    border-radius: 50%;
    background: var(--brand);
  }
  .brand-name {
    font-size: 36px;
    font-weight: 700;
    color: var(--brand);
    letter-spacing: 0.5px;
  }
  .holder-name {
    position: absolute;
    left: 36px;
    top: 84px;
    font-size: 27px;
    font-weight: 700;
  }
  .contact-list {
    position: absolute;
    left: 36px;
    bottom: 30px;
    list-style: none;
    font-size: 17px;
    line-height: 1.42;
  }
  .contact-list li { display: flex; align-items: center; gap: 12px; }
  .contact-list svg { width: 14px; height: 14px; fill: var(--ink); flex: none; }
  .service-list {
    position: absolute;
    left: 40px;
    bottom: 40px;
    list-style: none;
    font-size: 19px;
    line-height: 1.45;
  }
  .service-list li { display: flex; align-items: center; gap: 14px; }
  .service-list svg { width: 16px; height: 16px; flex: none; }
  .card-back .brand { top: 40px; }
</style>
</head>
<body>
  <section class="card card-front">
    <div class="music-staff" role="img" aria-label="Faint flowing music staff with treble clef and notes"></div>
    <div class="brand">
      <span class="brand-dot"></span>
      <span class="brand-name">ReelBloom</span>
    </div>
    <h1 class="holder-name">Your Name</h1>
    <ul class="contact-list">
      <li><svg viewBox="0 0 14 14"><path d="M4 1h6a1 1 0 0 1 1 1v10a1 1 0 0 1-1 1H4a1 1 0 0 1-1-1V2a1 1 0 0 1 1-1zm0 2v7h6V3z"/></svg>038-41260000</li>
      <li><svg viewBox="0 0 14 14"><path d="M3 1l3 3-1.5 2a8 8 0 0 0 3.5 3.5L10 8l3 3-2 2C6 13 1 8 1 3z"/></svg>912-52914400</li>
      <li><svg viewBox="0 0 14 14"><path d="M1 3h12v8H1zm1 1v.3l5 3.4 5-3.4V4z"/></svg>hello@reelbloom.com</li>
      <li><svg viewBox="0 0 14 14"><circle cx="7" cy="7" r="6"/></svg>www.reelbloom.com</li>
      <li><svg viewBox="0 0 14 14"><path d="M7 1a4.5 4.5 0 0 1 4.5 4.5C11.5 9 7 13 7 13S2.5 9 2.5 5.5A4.5 4.5 0 0 1 7 1zm0 3a1.5 1.5 0 1 0 0 3 1.5 1.5 0 0 0 0-3z"/></svg>4120, maple grove avenue Lakeview 58214</li>
    </ul>
  </section>

  <section class="card card-back">
    <div class="music-staff" role="img" aria-label="Faint flowing music staff with treble clef and notes"></div>
    <div class="brand">
      <span class="brand-dot"></span>
      <span class="brand-name">ReelBloom</span>
    </div>
    <ul class="service-list">
      <li><svg viewBox="0 0 16 16"><path d="M8 1v14M1 8h14M3 3l10 10M13 3L3 13" stroke="var(--accent)" stroke-width="1.8"/></svg>Training &amp; Enrichment</li>
      <li><svg viewBox="0 0 16 16"><path d="M8 1v14M1 8h14M3 3l10 10M13 3L3 13" stroke="var(--accent)" stroke-width="1.8"/></svg>Private &amp; Corporate Entertainment</li>
      <li><svg viewBox="0 0 16 16"><path d="M8 1v14M1 8h14M3 3l10 10M13 3L3 13" stroke="var(--accent)" stroke-width="1.8"/></svg>Music composition &amp; production</li>
    </ul>
  </section>
</body>
</html>
```